Brenlow Estates Website and Logo Design

We need a new logo and website designed for 'Brenlow Estates Ltd', which is a well established Guernsey property holding company founded in 1934.

The company does not currently have a website. The new website should be similar in style and layout to https://www.quorvanhall.example/.

Target Market(s)

Industry, Media, Tenants

Industry/Entity Type

Property Management

Logo Text

BEL OR Brenlow Estates Ltd OR BE

Coding

Coded - Design and coding required

Number of Pages Required

4 page

Font styles to use
Other font styles liked:
• Helvetica

Requirements
Must have
• The logo laying over the picture (like https://www.quorvanhall.example/).
• Big pictures on homepage (like https://www.quorvanhall.example/)

```html
<!DOCTYPE html>
<html lang="en">
<head>
<meta charset="utf-8">
<title>Brenlow Estates Ltd</title>
<link rel="stylesheet" href="https://fonts.googleapis.com/css2?family=Lora:wght@400;700&family=Open+Sans:wght@400;600;700&display=swap">
<style>
:root{
  --blue:#0a6cbf;
  --blue-dark:#0a5aa3;
  --ink:#333;
  --text:#666;
  --muted:#999;
  --line:#d6d6d6;
  --band:#f2f2f2;
  --white:#fff;
}
*{box-sizing:border-box;margin:0;padding:0}
html,body{width:739px;height:1200px;overflow:hidden;background:var(--white)}
body{position:relative;font-family:"Open Sans",Helvetica,Arial,sans-serif;color:var(--text)}
.abs{position:absolute}

/* hero */
.hero{left:0;top:0;width:739px;height:378px;background:linear-gradient(180deg,#b7c3cc 0%,#a9b6bf 22%,#5e7a63 26%,#3f6a6e 40%,#2d5b60 70%,#3c5552 100%)}
.site-header{left:0;top:0;width:739px;height:50px;background:rgba(236,238,240,.88)}
.brand{left:82px;top:15px;display:flex;align-items:center;gap:6px;font-family:"Lora",serif;font-size:14.5px;line-height:18px;color:var(--ink)}
.brand-mark{width:9px;height:9px;background:var(--ink)}
.nav{right:81px;top:19px;display:flex;gap:19px;font-family:"Lora",serif;font-size:7.5px;color:var(--ink);letter-spacing:.2px}
.nav .active{text-decoration:underline}
.hero-title{left:0;width:739px;top:176px;text-align:center;font-family:"Lora",serif;font-weight:700;font-size:18px;line-height:22px;color:var(--white);letter-spacing:.3px}
.hero-btn{left:333px;top:224px;width:73px;height:24px;background:var(--white);font-family:"Lora",serif;font-size:7.5px;color:var(--ink);display:flex;align-items:center;justify-content:center}
.slide-arrow{top:206px;width:18px;height:16px;background:rgba(0,0,0,.45)}
.slide-arrow.prev{left:16px}.slide-arrow.next{left:706px}

/* welcome */
.welcome-title{left:82px;top:418px;font-family:"Lora",serif;font-weight:700;font-size:19px;color:var(--blue)}
.welcome-sub{left:82px;top:440px;font-family:"Lora",serif;font-weight:400;font-size:13.5px;color:var(--ink)}
.welcome-copy{left:82px;top:466px;width:268px;font-size:6.4px;line-height:12.8px;text-align:justify}
.welcome-copy p+p{margin-top:4px}
.btn-outline{left:82px;top:602px;width:60px;height:25px;border:1px solid var(--line);font-family:"Lora",serif;font-size:7.5px;color:var(--ink);display:flex;align-items:center;justify-content:center}
.feature{left:389px;width:269px;height:99px;display:flex}
.feature-photo{width:176px;height:100%}
.feature-panel{flex:1;background:var(--blue);color:var(--white);text-align:right;padding:12px 11px 0 6px}
.feature-panel h3{font-family:"Lora",serif;font-weight:400;font-size:10px;line-height:13px}
.feature-panel p{font-size:5.2px;line-height:8.6px;margin-top:6px;color:#cfe2f4}
.feature-panel span{display:block;font-size:5.6px;font-weight:700;margin-top:6px}

/* listings */
.listings{left:0;top:676px;width:739px;height:242px;background:var(--band)}
.section-title{font-family:"Lora",serif;font-weight:400;font-size:14px;color:var(--blue)}
.listings-title{left:82px;top:706px}
.pager{top:710px;width:14px;height:13px;border:1px solid #888;background:var(--white)}
.listing{top:738px;width:134px;height:148px;background:var(--white)}
.listing-photo{width:134px;height:100px}
.listing-caption{padding:13px 14px 0;text-align:center;font-size:6.8px;line-height:11px;color:var(--muted)}

/* contact */
.contact-title{left:0;width:739px;top:956px;text-align:center}
.field{top:992px;width:134px;height:26px;border:1px solid var(--line);font-size:6.6px;color:var(--muted);padding:9px 10px}
.field.message{left:82px;top:1029px;width:576px}
.submit{left:345px;top:1069px;width:49px;height:24px;background:var(--blue-dark);color:var(--white);font-size:7.5px;font-weight:700;display:flex;align-items:center;justify-content:center}

/* footer */
.site-footer{left:0;top:1136px;width:739px;height:64px;background:var(--band)}
.footer-links{left:82px;top:1153px;font-size:6.8px;color:var(--text);word-spacing:1px}
.copyright{left:82px;top:1171px;font-size:6.8px;color:var(--text)}
.social{left:600px;top:1160px}
</style>
</head>
<body>

<div class="abs hero" role="img" aria-label="Harbour view with moored boats, a jetty and a green island under a grey sky"></div>

<header class="abs site-header"></header>
<div class="abs brand"><span class="brand-mark"></span><span>Brenlow Estates</span></div>
<nav class="abs nav">
  <span class="active">HOME</span><span>ABOUT</span><span>PROPERTIES</span><span>SERVICES</span><span>TESTIMONIALS</span><span>CONTACT US</span>
</nav>

<div class="abs hero-title">DONEC PURUS TELLUS<br>DICTUM SIT AMET</div>
<div class="abs hero-btn">CONTACT US</div>
<svg class="abs slide-arrow prev" viewBox="0 0 18 16"><path d="M11 4 L7 8 L11 12 M7 8 H13" stroke="#fff" stroke-width="1.6" fill="none"/></svg>
<svg class="abs slide-arrow next" viewBox="0 0 18 16"><path d="M7 4 L11 8 L7 12 M11 8 H5" stroke="#fff" stroke-width="1.6" fill="none"/></svg>

<h1 class="abs welcome-title">Welcome to</h1>
<h2 class="abs welcome-sub">Brenlow Estates Limited</h2>
<div class="abs welcome-copy">
  <p>Brenlow Estates Limited (BEL) is a family-owned Guernsey property holding company. It purchases properties that are considered to have potential for development either through refurbishment or by obtaining planning permission to change its classification from, for example, industrial premises to offices or retail outlets, or by the marriage value of buying an adjacent property to one already owned by BEL.</p>
  <p>BEL's reputation as a fair-minded landlord stems from the application of the founder's tenet of working with the tenant to help maximise the business benefits of both parties. There is no capital gains tax on the sale of property in the Island which makes buying and selling an attractive enterprise.</p>
</div>
<div class="abs btn-outline">Read more</div>

<div class="abs feature" style="top:422px">
  <div class="feature-photo" role="img" aria-label="Handshake over a desk with a small model house" style="background:linear-gradient(90deg,#d9dcdf 0%,#c8393b 30%,#e9e6e2 55%,#3a4150 85%,#eef0f2 100%)"></div>
  <div class="feature-panel"><h3>Pellentesque suscipit sapien</h3><p>Duis porttitor erat vitae nulla pharetra lacini donec lacus diam</p><span>READ MORE</span></div>
</div>
<div class="abs feature" style="top:528px">
  <div class="feature-photo" role="img" aria-label="Agent with a clipboard in a furnished hotel room" style="background:linear-gradient(90deg,#efe9e0 0%,#8f6a4c 45%,#a47a57 60%,#e8e3dc 100%)"></div>
  <div class="feature-panel"><h3>Aliquam erat volutpat</h3><p>Duis porttitor erat vitae nulla pharetra lacini donec lacus diam</p><span>READ MORE</span></div>
</div>

<section class="abs listings"></section>
<h2 class="abs section-title listings-title">Latest Listings</h2>
<svg class="abs pager" style="left:624px" viewBox="0 0 14 13"><path d="M8 3.5 L5 6.5 L8 9.5" stroke="#555" fill="none"/></svg>
<svg class="abs pager" style="left:644px" viewBox="0 0 14 13"><path d="M6 3.5 L9 6.5 L6 9.5" stroke="#555" fill="none"/></svg>

<div class="abs listing" style="left:82px">
  <div class="listing-photo" role="img" aria-label="Red brick detached house under a blue sky" style="background:linear-gradient(180deg,#3b78c4 0%,#7aa7d8 40%,#a0533b 60%,#6f8c4a 100%)"></div>
  <div class="listing-caption">Pellentesque suscipit sapien eu augue ultricies suscipit</div>
</div>
<div class="abs listing" style="left:229px">
  <div class="listing-photo" role="img" aria-label="Mediterranean villa with palm trees and a paved drive" style="background:linear-gradient(180deg,#2f79d0 0%,#6ea4de 35%,#c9a77e 60%,#c98a7a 100%)"></div>
  <div class="listing-caption">Pellentesque suscipit sapien eu augue ultricies suscipit</div>
</div>
<div class="abs listing" style="left:376px">
  <div class="listing-photo" role="img" aria-label="Grey two-storey family house with a garage" style="background:linear-gradient(180deg,#1856b3 0%,#3f7fcf 35%,#9aa3ad 60%,#5f9a47 100%)"></div>
  <div class="listing-caption">Pellentesque suscipit sapien eu augue ultricies suscipit</div>
</div>
<div class="abs listing" style="left:523px">
  <div class="listing-photo" role="img" aria-label="Modern white villa with a pool at dusk" style="background:linear-gradient(180deg,#2a4f8c 0%,#6f86a8 35%,#e6e0d6 55%,#2f7fa8 100%)"></div>
  <div class="listing-caption">Pellentesque suscipit sapien eu augue ultricies suscipit</div>
</div>

<h2 class="abs section-title contact-title">Contact Us</h2>
<div class="abs field" style="left:82px">Name</div>
<div class="abs field" style="left:229px">Email</div>
<div class="abs field" style="left:376px">Phone</div>
<div class="abs field" style="left:523px">Service Type
  <svg style="position:absolute;right:8px;top:11px" width="6" height="4" viewBox="0 0 6 4"><path d="M0.5 0.5 L3 3 L5.5 0.5" stroke="#888" fill="none"/></svg>
</div>
<div class="abs field message">Message</div>
<div class="abs submit">SUBMIT</div>

<footer class="abs site-footer"></footer>
<div class="abs footer-links">Home &nbsp;|&nbsp; About &nbsp;|&nbsp; Properties &nbsp;|&nbsp; Services &nbsp;|&nbsp; Testimonials &nbsp;|&nbsp; Contact Us</div>
<div class="abs copyright">Copyright &copy; 2016 Company name. All rights reserved.</div>
<svg class="abs social" width="58" height="16" viewBox="0 0 58 16" aria-label="Social links">
  <circle cx="8" cy="8" r="7.5" fill="#3b5998"/>
  <circle cx="29" cy="8" r="7.5" fill="#1da1f2"/>
  <circle cx="50" cy="8" r="7.5" fill="#0a6cbf"/>
</svg>

</body>
</html>
```